Velmora Nightclub Flyer (Updated)

Flyer for facebook, square is fine, or rectangular. Here is the text:
VELMORA
Nightclub + Lounge
presents

B2B THURSDAY
Nov 29 2018

CLUB FLOOR:
ROLF B2B GARTH
BENEDICT SALVORTE

LOUNGE:
TOBY B2B MY COUSIN
THUNDER REGGIE

Powered by KELP Acoustics
4726 8th Avenue 21+ 9pm-2am
velmorakestrel.com for VIP booth inquiries

Target Market(s)

Nightclub

Industry/Entity Type

Night Club

Font styles to use
Sans Serif

Colors

Designer to choose colors to be used in the design.

Requirements
Must have
• All the text listed, and plz keep the theme of the attached files. We want to stay consistent with the Velmora brand
Nice to have
• Try to stay with the theme from the attachments
Should not have
• Dont' stray to far from the general theme we have from the attachments

```html
<!DOCTYPE html>
<html lang="en">
<head>
<meta charset="utf-8">
<title>Velmora B2B Thursday Flyer</title>
<link rel="stylesheet" href="https://fonts.googleapis.com/css2?family=Montserrat:ital,wght@0,300;0,400;0,500;0,600;0,700&family=Russo+One&display=swap">
<style>
  :root {
    --page-bg: #f8f8f8;
    --flyer-light: #ffffff;
    --flyer-edge: #dedede;
    --ink: #2b2b2b;
    --ink-soft: #3a3a3a;
    --gold: #e4dd8a;
    --gold-deep: #b9a94e;
    --brown: #4a3d22;
    --brown-dark: #2a2114;
    --white: #ffffff;
  }
  * { box-sizing: border-box; margin: 0; padding: 0; }
  html, body {
    width: 1000px; height: 1200px; overflow: hidden;
    background: var(--page-bg);
    font-family: "Montserrat", sans-serif;
    color: var(--ink);
  }
  .flyer {
    position: absolute; left: 108px; top: 208px;
    width: 785px; height: 785px;
    background: radial-gradient(ellipse at 50% 42%, var(--flyer-light) 0%, #f4f4f4 55%, var(--flyer-edge) 100%);
    text-align: center;
  }
  .flyer > * { position: absolute; left: 0; width: 100%; }
  .brand-mark {
    left: 333px; top: 22px; width: 120px; height: 120px;
    border-radius: 50%; background: var(--gold);
  }
  .brand-name {
    top: 182px; font-size: 68px; font-weight: 400;
    letter-spacing: 3px; line-height: 1; color: var(--ink);
  }
  .brand-sub {
    top: 256px; font-size: 15px; font-weight: 500;
    letter-spacing: 1.8px; color: var(--ink-soft);
  }
  .presents {
    top: 284px; display: flex; justify-content: center; align-items: center; gap: 12px;
    font-size: 19px; font-weight: 500; letter-spacing: 1.5px; color: var(--ink-soft);
  }
  .presents .rule { width: 112px; height: 4px; background: var(--gold); }
  .event-title {
    top: 300px; font-family: "Russo One", sans-serif;
    font-size: 150px; line-height: 1.05; letter-spacing: 4px;
    color: var(--white);
    -webkit-text-stroke: 3px var(--brown-dark);
    text-shadow:
      2px 2px 0 #3d3219, 4px 4px 0 #54452a, 6px 6px 0 #6d5d33,
      8px 8px 0 #86763c, 10px 10px 0 #a09145, 12px 12px 0 #bcae55;
  }
  .event-day {
    top: 448px; font-size: 32px; font-weight: 600; letter-spacing: 2px; color: var(--ink);
  }
  .event-date {
    top: 486px; font-size: 22px; font-weight: 400; letter-spacing: 2px; color: var(--ink-soft);
  }
  .event-address {
    top: 525px; font-size: 19px; font-weight: 400; letter-spacing: 1.5px; color: var(--ink-soft);
  }
  .event-hours {
    top: 551px; font-size: 26px; font-weight: 700; letter-spacing: 1.5px; color: var(--ink);
  }
  .vip-pill {
    left: 282px; width: 228px; top: 588px; height: 32px; line-height: 32px;
    border-radius: 16px; background: var(--brown);
    color: var(--white); font-size: 17px; font-weight: 600;
  }
  .website {
    top: 626px; font-size: 18px; font-weight: 400; letter-spacing: 1px; color: var(--ink-soft);
  }
  .lineup {
    top: 662px; height: 84px; display: flex; align-items: center; justify-content: center;
  }
  .lineup .room {
    width: 186px; font-size: 15px; font-weight: 600; letter-spacing: 1px;
    line-height: 23px; color: var(--ink-soft);
  }
  .lineup .divider { width: 2px; height: 84px; background: var(--ink-soft); }
  .lineup .sponsor { width: 184px; color: var(--ink-soft); }
  .sponsor-label { font-size: 15px; font-weight: 600; letter-spacing: 1.5px; }
  .sponsor-name { font-size: 28px; font-weight: 600; letter-spacing: 3px; line-height: 1.1; margin-top: 2px; }
  .sponsor-tag { font-size: 15px; font-weight: 600; letter-spacing: 1.5px; }
  .lineup .room-left { margin-right: 0; }
</style>
</head>
<body>
  <main class="flyer">
    <div class="brand-mark" aria-hidden="true"></div>
    <h1 class="brand-name">VELMORA</h1>
    <p class="brand-sub">NIGHTCLUB + LOUNGE</p>
    <p class="presents"><span class="rule"></span>PRESENTS<span class="rule"></span></p>
    <h2 class="event-title">B2B</h2>
    <p class="event-day">THURSDAY</p>
    <p class="event-date">NOV | 29 | 2018</p>
    <p class="event-address">4726 8TH AVENUE 21+</p>
    <p class="event-hours">9PM-2AM</p>
    <p class="vip-pill">VIP booth inquiries</p>
    <p class="website">velmorakestrel.com</p>
    <section class="lineup">
      <div class="room room-left">CLUB FLOOR:<br>ROLF B2B GARTH<br>BENEDICT SALVORTE</div>
      <div class="divider"></div>
      <div class="sponsor">
        <div class="sponsor-label">POWERED BY</div>
        <div class="sponsor-name">KELP</div>
        <div class="sponsor-tag">ACOUSTICS</div>
      </div>
      <div class="divider"></div>
      <div class="room room-right">LOUNGE:<br>TOBY B2B MY COUSIN<br>THUNDER REGGIE</div>
    </section>
  </main>
</body>
</html>
```